international electric export business, needs help us Wordpress PSD design

we need a web page design, we are manufacturer and exporter of electric and electronic goods in China, for our products, you can visit our website: www.torvikel.com, now we would like to improve the page of torvikel.com, in order to get more attractive, We would like that it is simple and lookds confortable.
So we would like you to help us WORDPRESS PSD.
Target Market(s)
We are the factory and manufacture the low, medium and high voltage electric products, major export to South America, Middle East, Europe countries.
Our products used in construction and industry, similar Varnholt, QTL
Our customers are wholeseller, not retailer or end user.
Industry/Entity Type
Electronic
Font styles to use
Colors
Designer to choose colors to be used in the design.
Look and feel
Each slider illustrates characteristics of the customer's brand and the style your logo design should communicate.

```html
<!DOCTYPE html>
<html lang="en">
<head>
<meta charset="utf-8">
<title>Torvikel Electric</title>
<link href="https://fonts.googleapis.com/css2?family=PT+Sans:wght@400;700&family=Noto+Serif:ital,wght@1,700&display=swap" rel="stylesheet">
<style>
:root{
  --red:#c8090d;
  --red-dark:#a30508;
  --text:#333;
  --muted:#777;
  --line:#ddd;
  --panel:#f4f4f4;
  --dark:#3a3a3a;
}
*{box-sizing:border-box;margin:0;padding:0}
html,body{width:874px;height:1200px;overflow:hidden;background:#fff}
body{font-family:"PT Sans",sans-serif;color:var(--text);position:relative}
a{color:inherit;text-decoration:none}
.abs{position:absolute}
.top-links{right:92px;top:15px;font-size:10px;color:#555}
.top-links span{margin:0 4px;color:#999}
.brand{left:90px;top:32px;display:flex;align-items:center;gap:5px;white-space:nowrap}
.brand-mark{width:16px;height:16px;background:var(--red)}
.brand-name{font-size:20px;font-weight:700;color:var(--red);line-height:1}
.tagline{left:196px;top:36px;font-family:"Noto Serif",serif;font-style:italic;font-weight:700;font-size:16px;color:#aaa;border-left:1px solid #ccc;padding-left:7px;white-space:nowrap;line-height:22px}
.search{left:523px;top:52px;width:183px;height:22px;border:1px solid var(--line);font-size:8px;color:#999;font-style:italic;padding:6px 7px}
.search svg{position:absolute;right:6px;top:4px}
.lang{left:714px;top:52px;width:76px;height:22px;border:1px solid var(--line);font-size:10px;padding:4px 6px;display:flex;align-items:center;gap:5px}
.flag{width:14px;height:10px;background:#2a4b8f}
.nav{left:83px;top:86px;width:708px;height:36px;background:linear-gradient(#d8141a,var(--red-dark));border-radius:3px 3px 0 0;display:flex;padding-left:4px}
.nav a{color:#fff;font-size:13.5px;line-height:36px;padding:0 21px;border-right:1px solid #e84347}
.nav a:first-child{background:var(--red-dark);padding:0 22px}
.hero{left:83px;top:122px;width:708px;height:255px;border:1px solid var(--line);border-top:0;border-radius:0 0 4px 4px;background:linear-gradient(#fff,#ececec)}
.hero h1{position:absolute;left:42px;top:56px;font-weight:400;font-size:28px;color:#333}
.hero p{position:absolute;left:43px;top:94px;width:290px;font-size:10.5px;line-height:17.6px;color:#444}
.btn-dark{position:absolute;left:43px;top:155px;width:78px;height:24px;background:var(--dark);color:#fff;font-size:11px;border-radius:3px;text-align:center;line-height:24px}
.hero-img{position:absolute;left:375px;top:26px;width:270px;height:190px;border-radius:8px;background:radial-gradient(circle at 50% 55%,#d9d9d9,#f3f3f3 70%)}
.dots{position:absolute;left:328px;top:228px;display:flex;gap:4px}
.dots i{width:10px;height:10px;border-radius:50%;background:#bbb}
.dots i:first-child{background:#888}
.teaser{top:389px;width:231px;height:123px;border:1px solid var(--line);background:linear-gradient(#fff,#f6f6f6)}
.teaser h2{position:absolute;left:16px;top:12px;font-size:15px;font-weight:400;color:var(--red)}
.teaser .thumb{position:absolute;left:16px;top:37px;width:65px;height:64px;border:1px solid #ccc}
.teaser p{position:absolute;left:91px;top:36px;width:130px;font-size:8px;line-height:14px;color:var(--muted)}
.teaser .more{position:absolute;left:91px;top:97px;font-size:9px;color:#444}
.sidebar{left:83px;top:535px;width:172px;height:225px;border:1px solid var(--line)}
.sidebar h3{height:32px;background:var(--panel);border-bottom:1px solid var(--line);font-weight:400;font-size:14.5px;padding:8px 17px;color:#444}
.sidebar ul{list-style:none;padding:8px 14px 0 17px}
.sidebar li{font-size:9.5px;color:#555;height:21.5px;line-height:21px;border-bottom:1px solid #e6e6e6;padding-left:12px;position:relative}
.sidebar li:last-child{border:0}
.sidebar li::before{content:"›";position:absolute;left:0;color:#999;font-size:11px}
.recommend{left:269px;top:535px;width:521px;height:225px;border:1px solid var(--line)}
.recommend h3{position:absolute;left:21px;top:14px;font-weight:400;font-size:19px;color:#333}
.card{position:absolute;top:52px;width:110px}
.card .pimg{width:88px;height:75px;border:1px solid #ccc;background:linear-gradient(135deg,#f2f2f2,#c8c8c8)}
.card h4{font-weight:400;font-size:11.5px;margin-top:6px}
.card p{font-size:8px;line-height:13.5px;color:#555}
.btn-red{display:inline-block;margin-top:6px;width:59px;height:17px;background:var(--red);color:#fff;font-size:7.5px;font-weight:700;text-align:center;line-height:17px;border-radius:2px}
.divider{position:absolute;top:52px;width:1px;height:155px;background:var(--line)}
.about{left:88px;top:784px;width:475px}
.about h2{font-weight:400;font-size:19px;color:#333;margin-bottom:6px}
.about p{font-size:8.6px;line-height:16.5px;color:#444;margin-bottom:6px}
.chat{left:573px;top:782px;width:218px;height:131px;border:1px solid var(--line);overflow:hidden}
.chat .person{position:absolute;left:112px;top:16px;width:101px;height:113px;background:linear-gradient(#f7f3ef,#e9e1da);border-radius:4px}
.chat .t1{position:absolute;left:16px;top:10px;font-size:14px;color:#e0585b;z-index:1}
.chat .t2{position:absolute;left:16px;top:26px;font-size:15px;color:var(--red);z-index:1;white-space:nowrap}
.chat p{position:absolute;left:17px;top:48px;width:80px;font-size:7px;line-height:11.5px;color:#888;z-index:1}
.chat .get{position:absolute;left:15px;top:96px;width:48px;height:17px;border-radius:9px;background:var(--dark);color:#fff;font-size:6.5px;font-weight:700;text-align:center;line-height:17px;z-index:1}
.footer-band{left:0;top:960px;width:874px;height:20px;background:linear-gradient(#f0f0f0,#fff)}
.fcol{top:989px;border-right:1px solid var(--line);height:96px}
.fcol h5{font-weight:400;font-size:13px;color:var(--red);margin-bottom:6px}
.fcol li{list-style:none;font-size:9px;line-height:19.5px;color:#333}
.fcol.contact li{font-size:10px}
.pay{display:flex;gap:3px;margin-top:4px}
.pay i{width:28px;height:17px;border:1px solid #888;background:#e8ecf4}
.social{display:flex;gap:6px;margin-top:8px}
.social i{width:16px;height:16px;border-radius:2px;background:#5b7bb0}
.copy-line{left:0;top:1150px;width:874px;height:1px;background:#e2e2e2}
.copy{left:86px;top:1165px;font-size:8px;color:#888}
</style>
</head>
<body>
<div class="abs top-links">My Account<span>|</span>Wishlist<span>|</span>Free Shipping<span>|</span>My Cart</div>
<div class="abs brand"><span class="brand-mark"></span><span class="brand-name">Torvikel</span></div>
<div class="abs tagline">Science and techno reform the life.</div>
<div class="abs search">Search here..
  <svg width="12" height="12" viewBox="0 0 12 12"><circle cx="5" cy="5" r="3.8" fill="none" stroke="#666" stroke-width="1.5"/><line x1="8" y1="8" x2="11" y2="11" stroke="#666" stroke-width="1.8"/></svg>
</div>
<div class="abs lang"><span class="flag"></span>English <svg width="7" height="5"><path d="M0 0h7L3.5 5z" fill="#666"/></svg></div>

<nav class="abs nav"><a>Home</a><a>All Products</a><a>About Us</a><a>Services</a><a>Support</a><a>Contact Us</a></nav>

<section class="abs hero">
  <h1>Plastic Distribution Box</h1>
  <p>Plastic distribution box and metal distribution box are available in Torvikel. Distribution box is one common enclosure which used to install circuit breaker or fuse.</p>
  <a class="btn-dark">BUY NOW</a>
  <div class="hero-img" role="img" aria-label="Group of plastic distribution boxes and cable glands"></div>
  <div class="dots"><i></i><i></i><i></i><i></i></div>
</section>

<div class="abs teaser" style="left:83px">
  <h2>Latest News</h2>
  <div class="thumb" role="img" aria-label="Electrician working on a wall panel" style="background:linear-gradient(135deg,#e8e8e8,#3b5aa8)"></div>
  <p>Mauris vel lacus vitae felis vestibulum volutpat. Etiam est nunc, venenatis in, tristique eu, imperdiet ac, nisl.</p>
  <a class="more">Learn More ▸</a>
</div>
<div class="abs teaser" style="left:324px">
  <h2>Latest Products</h2>
  <div class="thumb" role="img" aria-label="Contactor product box" style="background:linear-gradient(135deg,#eee,#bbb)"></div>
  <p>Mauris vel lacus vitae felis vestibulum volutpat. Etiam est nunc, venenatis in, tristique eu, imperdiet ac, nisl.</p>
  <a class="more">Learn More ▸</a>
</div>
<div class="abs teaser" style="left:564px">
  <h2 style="top:23px">Hot Products</h2>
  <div class="thumb" role="img" aria-label="Gears and motor parts" style="top:48px;background:linear-gradient(135deg,#ddd,#888)"></div>
  <p style="top:47px">Mauris vel lacus vitae felis vestibulum volutpat. Etiam est nunc, venenatis in, tristique eu, imperdiet ac, nisl.</p>
  <a class="more" style="top:97px">Learn More ▸</a>
</div>

<aside class="abs sidebar">
  <h3>Our Products</h3>
  <ul>
    <li>Vivamus porttitor</li><li>Purus nisi eleifend</li><li>Libero tempus</li><li>Libero lectus feugiat</li>
    <li>Morbi diam mauris</li><li>Gravida mattis</li><li>Morbi eget arcu</li><li>Morbi porta</li>
  </ul>
</aside>

<section class="abs recommend">
  <h3>Recommend Product</h3>
  <div class="card" style="left:22px"><div class="pimg" role="img" aria-label="Push button switch product"></div><h4>Product Name</h4><p>vitae felis vestibulum<br>volutpat Etiam</p><a class="btn-red">BUY NOW</a></div>
  <div class="divider" style="left:128px"></div>
  <div class="card" style="left:152px"><div class="pimg" role="img" aria-label="Square push button product"></div><h4>Product Name</h4><p>vitae felis vestibulum<br>volutpat Etiam</p><a class="btn-red">BUY NOW</a></div>
  <div class="divider" style="left:255px"></div>
  <div class="card" style="left:281px"><div class="pimg" role="img" aria-label="Emergency stop button product"></div><h4>Product Name</h4><p>vitae felis vestibulum<br>volutpat Etiam</p><a class="btn-red">BUY NOW</a></div>
  <div class="divider" style="left:392px"></div>
  <div class="card" style="left:411px"><div class="pimg" role="img" aria-label="Wall switch product"></div><h4>Product Name</h4><p>vitae felis vestibulum<br>volutpat Etiam</p><a class="btn-red">BUY NOW</a></div>
</section>

<section class="abs about">
  <h2>About Our Company</h2>
  <p>Torvikel Electric Enterprises is one of specialized manufacturers and exporters in line of low, middle and high voltage electric equipments. More than 15 years manufacture and export experience, technology and quality of products and our service win high reputation from the old and new customers around the world, 12 countries sole agents has signed successfully, another creating branch company in Lima, Peru and Lattakia, Syria.</p>
  <p>Phasellus felis dolor, scelerisque a, tempus eget, lobortis id, libero. Donec scelerisque leo ac risus. Praesent sit amet est. In dictum, dolor eu dictum porttitor, enim felis viverra mi, eget luctus massa purus quis odio.</p>
</section>

<aside class="abs chat">
  <div class="person" role="img" aria-label="Smiling support agent giving thumbs up"></div>
  <div class="t1">Live Chat</div>
  <div class="t2">Online Exchange</div>
  <p>Lorem ipsum dolor sit amet, consectetuer adipiscing elit. Nam cursus Morbi</p>
  <a class="get">GET NOW</a>
</aside>

<div class="abs footer-band"></div>
<div class="abs fcol" style="left:88px;width:113px"><h5>All Products</h5><ul><li>All Products</li><li>What's New</li><li>Recommend Products</li><li>Download Products</li></ul></div>
<div class="abs fcol" style="left:225px;width:80px"><h5>About Us</h5><ul><li>About Us</li><li>Latest News</li><li>Advantages</li><li>Certification</li></ul></div>
<div class="abs fcol" style="left:333px;width:106px"><h5>Services</h5><ul><li>Site Map</li><li>Web Links</li><li>Privacy Policy</li><li>Terms and Conditions</li></ul></div>
<div class="abs fcol contact" style="left:462px;width:128px"><h5>Contact Us</h5><ul><li>Tel: 0086-577-20140101</li><li>Fax: 0086-577-20140102</li><li>M.B: 0086-13900112233</li><li>Skype: torvikel2008</li></ul></div>
<div class="abs fcol" style="left:609px;width:150px;border:0"><h5>Make Payment</h5>
  <div class="pay"><i></i><i></i><i></i><i style="width:48px"></i></div>
  <div class="social"><i></i><i style="background:#6ab4de"></i><i style="background:#2a6aa8"></i><i style="background:#f08a24"></i></div>
</div>

<div class="abs copy-line"></div>
<div class="abs copy">© 2013 Company Name. All right reserved. Term of Use</div>
</body>
</html>
```